Harborline Auto LLC

Car Dealer Customer Service
Address: 2874 Cresthaven Road, Shelbyville, TN 37162
web: www.harborlineautoxq.net
email: harborlineautoxq@mailnest.example
Phone: (931) 555-0148
Phone: (629) 555-0173

```html
<!DOCTYPE html>
<html lang="en">
<head>
<meta charset="utf-8">
<title>Harborline Auto – Business Card</title>
<link href="https://fonts.googleapis.com/css2?family=Poppins:wght@400;600;700&display=swap" rel="stylesheet">
<style>
  :root {
    --backdrop: #2d2d2f;
    --card-top: #2a2a2e;
    --card-bottom: #1f1f22;
    --brand-blue: #2b88c8;
    --accent-gold: #e3aa3c;
    --text-light: #e6e6e8;
    --rule: #8a8a8e;
    --emboss: #151517;
  }
  * { margin: 0; padding: 0; box-sizing: border-box; }
  html, body { width: 1200px; height: 1138px; overflow: hidden; }
  body {
    background: var(--backdrop);
    font-family: "Poppins", sans-serif;
    position: relative;
  }
  .card {
    position: absolute;
    left: 274px;
    width: 622px;
    height: 376px;
    border-radius: 16px;
    background: linear-gradient(160deg, var(--card-top), var(--card-bottom));
    box-shadow: 0 6px 14px rgba(0,0,0,0.45);
    overflow: hidden;
  }
  .card--front { top: 186px; }
  .card--back { top: 607px; }

  .front-mark {
    position: absolute;
    left: 0; right: 0; top: 160px;
    text-align: center;
    font-weight: 700;
    font-size: 34px;
    letter-spacing: 1px;
    color: var(--emboss);
  }
  .front-web {
    position: absolute;
    left: 0; right: 0; top: 333px;
    display: flex; justify-content: center; align-items: center; gap: 22px;
    color: var(--text-light);
    font-size: 14px;
  }
  .front-web .dash { width: 52px; height: 2px; background: var(--accent-gold); }

  .brand-dot {
    position: absolute;
    left: 470px; top: 38px;
    width: 96px; height: 96px;
    border-radius: 50%;
    background: var(--brand-blue);
  }
  .brand-name {
    position: absolute;
    right: 32px; top: 160px;
    font-weight: 700;
    font-size: 22px;
    color: var(--brand-blue);
    letter-spacing: 0.5px;
  }
  .person-name {
    position: absolute;
    left: 27px; top: 200px;
    font-weight: 700; font-size: 23px;
    color: var(--brand-blue);
  }
  .person-title {
    position: absolute;
    left: 27px; top: 232px;
    font-size: 15px;
    color: var(--text-light);
  }
  .divider {
    position: absolute;
    left: 27px; top: 264px;
    width: 569px; height: 1px;
    background: var(--rule);
  }
  .contact {
    position: absolute;
    display: flex; align-items: center; gap: 9px;
    font-size: 15px;
    color: var(--text-light);
    white-space: nowrap;
  }
  .contact svg { width: 16px; height: 16px; flex: none; }
  .contact--phone { font-weight: 600; color: var(--brand-blue); letter-spacing: 0.5px; }
  .contact--online { letter-spacing: 0.6px; font-size: 15px; }
</style>
</head>
<body>

<section class="card card--front">
  <div class="front-mark">HARBORLINE AUTO</div>
  <div class="front-web">
    <span class="dash"></span>
    <span>www.harborlineautoxq.net</span>
    <span class="dash"></span>
  </div>
</section>

<section class="card card--back">
  <div class="brand-dot"></div>
  <div class="brand-name">HARBORLINE AUTO</div>

  <div class="person-name">Daniel Marsh</div>
  <div class="person-title">Managing Director</div>
  <div class="divider"></div>

  <div class="contact contact--phone" style="left:27px; top:278px;">
    <svg viewBox="0 0 16 16" fill="none" stroke="#e3aa3c" stroke-width="1.4"><circle cx="8" cy="8" r="7"/><path d="M5.5 4.5l1.3 1.6-.8 1c.6 1.2 1.5 2.1 2.7 2.7l1-.8 1.6 1.3-.8 1.2C7.8 11.3 4.7 8.2 4.5 5.3z" fill="#e3aa3c" stroke="none"/></svg>
    <span>931-555-0148</span>
  </div>
  <div class="contact contact--phone" style="left:27px; top:300px;">
    <svg viewBox="0 0 16 16" fill="none" stroke="#e3aa3c" stroke-width="1.4"><circle cx="8" cy="8" r="7"/><path d="M5.5 4.5l1.3 1.6-.8 1c.6 1.2 1.5 2.1 2.7 2.7l1-.8 1.6 1.3-.8 1.2C7.8 11.3 4.7 8.2 4.5 5.3z" fill="#e3aa3c" stroke="none"/></svg>
    <span>629-555-0173</span>
  </div>
  <div class="contact" style="left:27px; top:328px;">
    <svg viewBox="0 0 16 16" fill="none" stroke="#e3aa3c" stroke-width="1.4"><path d="M8 15s5-5 5-8.5A5 5 0 0 0 3 6.5C3 10 8 15 8 15z"/><circle cx="8" cy="6.5" r="1.8"/></svg>
    <span>2874 Cresthaven Road, Shelbyville, TN 37162</span>
  </div>

  <div class="contact contact--online" style="left:235px; top:278px;">
    <svg viewBox="0 0 16 16" fill="none" stroke="#e3aa3c" stroke-width="1.3"><rect x="1.5" y="3.5" width="13" height="9" rx="1"/><path d="M1.5 4l6.5 5 6.5-5"/></svg>
    <span>www.harborlineautoxq.net</span>
  </div>
  <div class="contact contact--online" style="left:235px; top:300px;">
    <svg viewBox="0 0 16 16" fill="none" stroke="#e3aa3c" stroke-width="1.2"><circle cx="8" cy="8" r="6.5"/><ellipse cx="8" cy="8" rx="2.8" ry="6.5"/><path d="M1.5 8h13M2.5 4.8h11M2.5 11.2h11"/></svg>
    <span>harborlineautoxq@mailnest.example</span>
  </div>
</section>

</body>
</html>
```